Payment company requires web design

We need a web design for a new company based in Singapore.

The company focuses on providing 2 key products: 1) an alternative payment option (i.e. like quib or trelloquin options) on the traditional checkout process 2) a replacement/outsource of a merchants payment page. Key in the UX flow is a end customer dashboard that manages all payments.

We look to provide a simple, fluid and easy to use payment process. The dashboard is minimalistic that allows easy navigation, review of transactions and all available options through gamification.

The final design should communicate ease of use, flexibility and transparency.

Target Market(s)

The value is for the merchant - retail/travel/insurance companies. However its the merchant's end customers that are the target and who the UX is built for.

Industry/Entity Type

It Company

Logo Text

zelnar

Number of Pages Required

5+ page

Colors
ec1f27

Requirements
Must have
• 7 pages mimicking UX flow
• payment page * 2 - 1) alternative payment type 2) outsource of merchants payment page to our business
• our landing page
• end customer verification page
• end customer registration
• customer dashboard
• UX flow in attached file
Nice to have
• open to ideas
• have asked for the logo to be added
• logo to have the colour red (chinese for prosperity)
• the company is all about flexibility, transparency in personal finance management with the option of instalment payments

```html
<!DOCTYPE html>
<html lang="en">
<head>
<meta charset="utf-8">
<title>Zelnar – Payment Processing</title>
<link href="https://fonts.googleapis.com/css2?family=Montserrat:wght@300;400;500;600;800&display=swap" rel="stylesheet">
<style>
:root{
  --brand-red:#ec1f27;
  --white:#ffffff;
  --ink:#2a2a2a;
  --body-text:#3a3a3a;
  --hero-top:#b9b3ad;
  --hero-mid:#a49c9a;
  --hero-low:#c9c6cc;
}
*{margin:0;padding:0;box-sizing:border-box}
html,body{width:1200px;height:1185px;overflow:hidden;background:var(--white)}
body{font-family:'Montserrat',sans-serif;position:relative;color:var(--body-text)}

.hero{position:absolute;left:0;top:0;width:1200px;height:634px;
  background:
    radial-gradient(ellipse 420px 260px at 520px 330px, rgba(214,178,166,.55), transparent 70%),
    radial-gradient(ellipse 300px 200px at 520px 220px, rgba(40,40,45,.35), transparent 70%),
    linear-gradient(180deg,var(--hero-top) 0%,var(--hero-mid) 45%,var(--hero-low) 80%,#8f8c90 100%);}

.site-header{position:absolute;left:0;top:0;width:1200px;height:94px;border-bottom:1px solid rgba(255,255,255,.22)}
.logo{position:absolute;left:132px;top:26px;font-size:38px;font-weight:800;color:var(--white);letter-spacing:-.5px}
.main-nav{position:absolute;top:40px;left:512px;display:flex;gap:0;font-size:13px;font-weight:500;color:var(--white)}
.main-nav span{position:absolute;white-space:nowrap}
.btn-login{position:absolute;left:933px;top:35px;width:71px;height:28px;border:1px solid rgba(255,255,255,.75);color:var(--white);font-size:13px;font-weight:500;text-align:center;line-height:26px}
.link-signup{position:absolute;left:1022px;top:41px;color:var(--white);font-size:13px;font-weight:500}

.hero-copy{position:absolute;left:132px;top:220px;color:var(--white)}
.hero-kicker{font-size:35px;font-weight:400;line-height:44px}
.hero-title{font-size:48px;font-weight:600;line-height:52px}
.hero-sub{font-size:27px;font-weight:400;line-height:40px;margin-top:2px}
.btn-register{position:absolute;left:133px;top:386px;width:145px;height:41px;background:var(--brand-red);color:var(--white);font-size:17px;text-align:center;line-height:41px;border-radius:2px}

.slider-arrow{position:absolute;top:275px;width:44px;height:44px}
.slider-arrow.prev{left:45px}
.slider-arrow.next{left:1111px}

.faq{position:absolute;left:0;top:634px;width:1200px;height:480px}
.faq-title{position:absolute;left:0;width:1200px;top:26px;text-align:center;font-size:38px;font-weight:300;color:var(--ink)}
.faq-item{position:absolute;left:133px;width:880px;font-size:11.2px;line-height:21.6px;color:var(--body-text)}
.faq-item .tag{color:var(--brand-red);font-size:13px}
.faq-item .cont{padding-left:22px}

.site-footer{position:absolute;left:0;top:1114px;width:1200px;height:71px;background:var(--brand-red);color:var(--white);font-size:14px}
.site-footer p{position:absolute;left:132px;top:26px}
</style>
</head>
<body>

<div class="hero" role="img" aria-label="Photo of hands holding a payment card over a laptop keyboard"></div>

<header class="site-header">
  <div class="logo">Zelnar</div>
  <nav class="main-nav">
    <span style="left:0">About</span>
    <span style="left:68px">Services</span>
    <span style="left:147px">Web</span>
    <span style="left:206px">Technology</span>
    <span style="left:306px">Contact Us</span>
  </nav>
  <div class="btn-login">Login</div>
  <div class="link-signup">Sign Up</div>
</header>

<svg class="slider-arrow prev" viewBox="0 0 44 44" aria-hidden="true">
  <circle cx="22" cy="22" r="22" fill="rgba(0,0,0,.12)"/>
  <polyline points="26,8 14,22 26,36" fill="none" stroke="#fff" stroke-width="1.2"/>
</svg>
<svg class="slider-arrow next" viewBox="0 0 44 44" aria-hidden="true">
  <circle cx="22" cy="22" r="22" fill="rgba(0,0,0,.06)"/>
  <polyline points="18,8 30,22 18,36" fill="none" stroke="#fff" stroke-width="1.2"/>
</svg>

<section class="hero-copy">
  <div class="hero-kicker">We are payment</div>
  <h1 class="hero-title">Processing Company</h1>
  <div class="hero-sub">from Singapore</div>
</section>
<div class="btn-register">Register Now!</div>

<section class="faq">
  <h2 class="faq-title">FAQ</h2>
  <div class="faq-item" style="top:88px"><span class="tag">Q:-</span> Quis autem vel eum iure reprehenderit qui in ea voluptate velit esse quam nihil molestiae consequatur, vel illum qui dolorem<br><span class="cont">eum fugiat quo voluptas nulla &nbsp; pariatur?</span></div>
  <div class="faq-item" style="top:144px;width:900px"><span class="tag">A:-</span> But I must explain to you how all this mistaken idea of denouncing pleasure and praising pain was born and I will give you a complete Nemo enim ipsam<br><span class="cont">voluptatem quia &nbsp;&nbsp;&nbsp; voluptas sit aspernatur aut odit aut fugit, sed quia consequuntur magni dolores eos qui ratione voluptatem sequi nesciunt</span></div>
  <div class="faq-item" style="top:224px"><span class="tag">Q:-</span> Ut enim ad minima veniam, quis nostrum exercitationem ullam corporis suscipit laboriosam, nisi ut aliquid ex ea commodi consequatur?</div>
  <div class="faq-item" style="top:264px;width:900px"><span class="tag">A:-</span> At vero eos et accusamus et iusto odio dignissimos ducimus qui blanditiis praesentium voluptatum deleniti atque corrupti quos dolores et quas molestias<br><span class="cont">excepturi sint occaecati cupiditate non provident, similique sunt in culpa qui officia deserunt mollitia animi, id est laborum et dolorum fuga.</span></div>
  <div class="faq-item" style="top:352px"><span class="tag">Q:-</span> Who chooses to enjoy a pleasure that has no annoying consequences, or one who avoids a pain that produces no resultant pleasure?</div>
  <div class="faq-item" style="top:392px;width:900px"><span class="tag">A:-</span> Nam libero tempore, cum soluta nobis est eligendi optio cumque nihil impedit quo minus id quod maxime placeat facere possimus, omnis voluptas<br><span class="cont">assumenda est, omnis dolor repellendus.</span></div>
</section>

<footer class="site-footer">
  <p>© 2016 Zelnar . All right reserved &nbsp;Term of Use</p>
</footer>

</body>
</html>
```